We need a business card design, letterhead design and envelope design for our corporate image

We are looking for a corporate business card design, letterhead and envelope design to match the business card design. Logo is done.

```html
<!DOCTYPE html>
<html lang="en">
<head>
<meta charset="utf-8">
<title>Norvane – Business Card</title>
<link href="https://fonts.googleapis.com/css2?family=Open+Sans:wght@400;600;700&display=swap" rel="stylesheet">
<style>
  :root {
    --stage: #3b3b3b;
    --stage-dark: #2e2e2e;
    --card: #1d1d1d;
    --accent: #f5c400;
    --text-light: #e6e6e6;
    --text-muted: #bdbdbd;
  }
  * { box-sizing: border-box; margin: 0; padding: 0; }
  html, body {
    width: 1200px; height: 801px; overflow: hidden;
  }
  body {
    background: radial-gradient(ellipse at 60% 40%, var(--stage) 0%, var(--stage-dark) 100%);
    font-family: "Open Sans", Arial, sans-serif;
    position: relative;
  }
  .card {
    position: absolute;
    top: 252px;
    width: 520px;
    height: 297px;
    background: var(--card);
    border: 2px solid var(--accent);
    box-shadow: 0 18px 40px rgba(0,0,0,0.45);
  }
  .card--info { left: 50px; }
  .card--brand { left: 630px; }

  /* Info side */
  .identity {
    position: absolute;
    left: 70px; top: 96px;
    width: 200px;
    text-align: right;
  }
  .identity__name {
    color: var(--accent);
    font-weight: 700;
    font-size: 22px;
    letter-spacing: 0.5px;
    text-transform: uppercase;
  }
  .identity__role {
    color: var(--text-muted);
    font-size: 15px;
    margin-top: 2px;
  }
  .divider {
    position: absolute;
    left: 290px; top: 88px;
    width: 1.5px; height: 68px;
    background: var(--accent);
  }
  .contacts {
    position: absolute;
    left: 308px; top: 86px;
    list-style: none;
  }
  .contacts li {
    display: flex; align-items: center;
    gap: 7px;
    color: var(--text-light);
    font-size: 13.5px;
    line-height: 24px;
  }
  .contacts svg { width: 12px; height: 12px; flex: none; }
  .address {
    position: absolute;
    left: 0; right: 0; bottom: 58px;
    text-align: center;
    color: var(--text-light);
    font-size: 14.5px;
    letter-spacing: 0.2px;
  }

  /* Brand side */
  .brand {
    position: absolute;
    left: 50%; top: 50%;
    transform: translate(-50%, -50%);
    display: flex; align-items: center; gap: 16px;
  }
  .brand__mark {
    width: 44px; height: 44px;
    background: var(--accent);
  }
  .brand__name {
    color: var(--accent);
    font-weight: 700;
    font-size: 52px;
    line-height: 1;
    letter-spacing: -1px;
  }
</style>
</head>
<body>
  <section class="card card--info">
    <div class="identity">
      <p class="identity__name">Alex Marlow</p>
      <p class="identity__role">President</p>
    </div>
    <div class="divider"></div>
    <ul class="contacts">
      <li>
        <svg viewBox="0 0 12 12" aria-hidden="true"><path fill="#f5c400" d="M2.5 1l2 2.2-1 1.3c.7 1.5 1.6 2.4 3 3l1.3-1L10 8.5 9 10.6C5 10.6 1.4 7 1.4 3z"/></svg>
        555-310-4827
      </li>
      <li>
        <svg viewBox="0 0 12 12" aria-hidden="true"><rect x="1" y="2.5" width="10" height="7" fill="#f5c400"/><path d="M1 2.8l5 3.6 5-3.6" fill="none" stroke="#1d1d1d" stroke-width="1"/></svg>
        amarlow@norvane.com
      </li>
      <li>
        <svg viewBox="0 0 12 12" aria-hidden="true"><circle cx="6" cy="6" r="5" fill="none" stroke="#f5c400" stroke-width="1.3"/><ellipse cx="6" cy="6" rx="2" ry="5" fill="none" stroke="#f5c400" stroke-width="1"/><path d="M1 6h10" stroke="#f5c400" stroke-width="1"/></svg>
        www.norvane.com
      </li>
    </ul>
    <p class="address">1840 Harbor View Drive, Seacliff CA 90417</p>
  </section>

  <section class="card card--brand">
    <div class="brand">
      <span class="brand__mark"></span>
      <span class="brand__name">Norvane</span>
    </div>
  </section>
</body>
</html>
```